brqnal new business card design project

we need a new business card design. you can view info about us @ brqnal-example.com. i have attached an example of our previous card with our previous name that we no longer use. We really liked the design, colors etc. look below to see more info about this project. it asks for a limited number of words. please see our website for more info about our compnay.

Target Market(s)

law enforcement

Contact Information for Business Card

i have uploaded an example of what we used before that we liked.

Font styles to use
Serif

```html
<!DOCTYPE html>
<html lang="en">
<head>
<meta charset="utf-8">
<title>Brqnal business card</title>
<link rel="stylesheet" href="https://fonts.googleapis.com/css2?family=Open+Sans:wght@300;400;600&family=Roboto:wght@700&display=swap">
<style>
  :root {
    --page-bg: #d3d7d8;
    --brand-blue: #2575bf;
    --ink-black: #050505;
    --paper-white: #ffffff;
    --night-navy: #0b1a26;
    --map-glow: #1f6f95;
    --map-deep: #0e2c40;
  }
  * { margin: 0; padding: 0; box-sizing: border-box; }
  html, body { width: 1200px; height: 923px; overflow: hidden; }
  body {
    background: var(--page-bg);
    font-family: "Open Sans", Arial, sans-serif;
    position: relative;
  }
  .card {
    position: absolute;
    top: 307px;
    width: 540px;
    height: 309px;
    overflow: hidden;
    box-shadow: 0 12px 30px rgba(0,0,0,0.18);
  }
  .card--front { left: 45px; background: var(--brand-blue); }
  .card--back { left: 615px; background: var(--night-navy); }

  .card__shapes { position: absolute; inset: 0; }

  .brand-name {
    position: absolute;
    color: var(--paper-white);
    font-weight: 300;
    letter-spacing: 6px;
    line-height: 1;
  }
  .card--front .brand-name { right: 40px; top: 112px; font-size: 50px; }
  .card--back .brand-name { left: 120px; top: 118px; font-size: 56px; }

  .holder-name {
    position: absolute;
    left: 58px; top: 168px;
    font-family: "Roboto", Arial, sans-serif;
    font-weight: 700;
    font-size: 19px;
    color: var(--ink-black);
  }
  .contact-list {
    position: absolute;
    left: 26px; top: 204px;
    list-style: none;
    color: var(--paper-white);
    font-size: 14px;
    line-height: 20px;
  }
  .contact-list li { display: flex; align-items: center; gap: 9px; }
  .contact-list svg { width: 12px; height: 12px; fill: var(--brand-blue); flex: none; }
  .address {
    position: absolute;
    right: 30px; bottom: 24px;
    text-align: right;
    color: var(--paper-white);
    font-size: 14px;
    line-height: 20px;
  }

  .network-map {
    position: absolute;
    left: 110px; top: 40px;
    width: 330px; height: 200px;
    border-radius: 40% 46% 38% 44%;
    background: radial-gradient(ellipse at 40% 70%, var(--map-glow) 0%, var(--map-deep) 60%, transparent 100%);
  }
  .web-line {
    position: absolute;
    left: 22px; bottom: 26px;
    color: var(--paper-white);
    font-size: 14px;
  }
  .blue-band {
    position: absolute;
    left: 0; right: 0; bottom: 0;
    height: 20px;
    background: var(--brand-blue);
    border-top: 3px solid var(--paper-white);
  }
</style>
</head>
<body>

<section class="card card--front" aria-label="Card front">
  <svg class="card__shapes" viewBox="0 0 540 309" aria-hidden="true">
    <polygon points="0,160 222,160 236,190 0,190" fill="var(--paper-white)"/>
    <polygon points="0,190 236,190 252,220 540,246 540,309 0,309" fill="var(--ink-black)"/>
    <polyline points="222,160 240,208 540,234" fill="none" stroke="var(--paper-white)" stroke-width="4"/>
  </svg>
  <div class="brand-name">BRQNAL</div>
  <div class="holder-name">Dana Reyes</div>
  <ul class="contact-list">
    <li><svg viewBox="0 0 24 24"><path d="M6.6 10.8a15 15 0 0 0 6.6 6.6l2.2-2.2a1 1 0 0 1 1-.25 11 11 0 0 0 3.6.6 1 1 0 0 1 1 1V20a1 1 0 0 1-1 1A17 17 0 0 1 3 4a1 1 0 0 1 1-1h3.5a1 1 0 0 1 1 1 11 11 0 0 0 .6 3.6 1 1 0 0 1-.25 1z"/></svg>555.010.4477</li>
    <li><svg viewBox="0 0 24 24"><path d="M2 5h20v14H2z M2 5l10 8 10-8" stroke="#fff" stroke-width="1"/></svg>info@brqnal-example.com</li>
    <li><svg viewBox="0 0 24 24"><circle cx="12" cy="12" r="10"/><path d="M2 12h20M12 2c3 3 3 17 0 20M12 2c-3 3-3 17 0 20" stroke="#000" stroke-width="1.5" fill="none"/></svg>www.brqnal-example.com</li>
  </ul>
  <div class="address">4120 Larkfield Road<br>Austin, TX 78701</div>
</section>

<section class="card card--back" aria-label="Card back">
  <div class="network-map" role="img" aria-label="Glowing network map of connected points across the country"></div>
  <div class="brand-name">BRQNAL</div>
  <div class="web-line">www.brqnal-example.com</div>
  <div class="blue-band"></div>
</section>

</body>
</html>
```